Harbor Seal Works Spray Foam Appications website

We need a custom website for our company, www.harborsealworks.example. We need something we can modify by adding/changing content, photos, updated projects, etc. We are a commercial contractor specializing in Spray Foam applications. We want the website to be very creative and easy to navigate. The main points of the website are to showcase our projects, and describe our scope of services. We provide spray foam applications to the residential and commercial market. We offer Spray Foam roofing applications, as well as Spray Foam interior insulation applications. We also provide Roof Restoration Coating Systems to refurbish old and failing metal roofs. We would be ok with a one page web design if we can get the scope of our services to flow in a single page. The designer can decide if single or multiple pages works best for our business. One of the suppliers we work with is www.verdansupply.example.

Target Market(s)

Residential Home Builders, General Contractors, Commercial Construction Companies, Property Management Groups.

Industry/Entity Type

Insulation

Number of Pages Required

5+ page

Font styles to use
Serif
Sans Serif

Colors

Designer to choose colors to be used in the design.

Requirements
Must have
• We already have a Wix page, so website must be a Wix theme design. Nice easy to navigate format. Color matched to our current logo theme. We already have brochures and would like for it to match what's already in the hands of some of our customers. Need to be able to manage content to update photos, projects, scope of service, etc., via Wix. Current hold/splash page is hosted at www.harborsealworks.example. We would also like to have this video posted on the home page: https://www.videohost.example/watch?v=QxT4pLm9ZrA&feature=share
Nice to have
• I have attached some splash videos, being able to incorporate these somehow without being overpowering would be nice.

```html
<!DOCTYPE html>
<html lang="en">
<head>
<meta charset="utf-8">
<title>Harbor Seal Works</title>
<link href="https://fonts.googleapis.com/css2?family=Raleway:wght@300;400;500;600;700&display=swap" rel="stylesheet">
<style>
:root{
  --yellow:#f3b11e;
  --ink:#1f1f1f;
  --muted:#a3a3a3;
  --line:#e3e3e3;
  --footer:#232323;
  --footer-line:#3a3a3a;
  --white:#ffffff;
}
*{box-sizing:border-box;margin:0;padding:0}
html,body{width:724px;height:1200px;overflow:hidden;background:var(--white)}
body{font-family:'Raleway',sans-serif;color:var(--ink)}
.page{position:relative;width:724px;height:1200px;overflow:hidden}
.abs{position:absolute}

/* News */
.section-title{position:absolute;left:0;width:724px;top:40px;text-align:center;font-size:18px;font-weight:700;letter-spacing:.2px}
.section-title span{color:var(--yellow)}
.title-rule{position:absolute;left:350px;width:36px;height:1px;background:var(--yellow)}
.news-photo{position:absolute;top:100px;width:167px;height:167px}
.news-card{position:absolute;top:259px;width:158px;height:121px;background:var(--white);box-shadow:0 1px 4px rgba(0,0,0,.08);text-align:center}
.news-card h3{margin-top:23px;font-size:12.6px;font-weight:500;line-height:22.5px}
.news-card.active h3{color:var(--yellow)}
.news-card .rule{width:36px;height:1px;background:var(--ink);margin:7px auto 0}
.news-card.active .rule{background:var(--line)}
.news-card .meta{margin-top:13px;font-size:5px;color:#555}
.news-card .meta b{color:var(--ink);font-weight:600}
.news-card.active{border-bottom:1.5px solid var(--yellow)}
.more{position:absolute;left:50%;bottom:-9px;margin-left:-9px;width:18px;height:18px;border-radius:50%;background:var(--white);box-shadow:0 1px 3px rgba(0,0,0,.18);display:flex;align-items:center;justify-content:center}
.news-card.active .more{background:var(--yellow)}

/* Partner band */
.partners{position:absolute;left:0;top:426px;width:724px;height:135px;background:var(--yellow)}
.badge{position:absolute;top:40px;width:62px;height:52px}

/* Quote */
.worker-photo{position:absolute;left:0;top:596px;width:209px;height:323px}
.quote-title{position:absolute;left:232px;top:638px;font-size:18.5px;font-weight:700}
.quote-rule{position:absolute;left:232px;top:665px;width:37px;height:1px;background:var(--yellow)}
.feature{position:absolute;left:232px;width:170px}
.feature svg{position:absolute;left:0;top:2px}
.feature h4{position:absolute;left:32px;top:0;font-size:7.4px;font-weight:500;letter-spacing:.8px;white-space:nowrap}
.feature .sub{position:absolute;left:32px;top:10px;font-size:5.8px;color:var(--yellow);letter-spacing:.6px}
.feature p{position:absolute;left:32px;top:22px;width:145px;font-size:6.3px;line-height:13.6px;color:var(--muted);letter-spacing:.55px;font-weight:300}

.quote-form{position:absolute;left:414px;top:638px;width:212px;height:246px;background:var(--white);box-shadow:0 1px 5px rgba(0,0,0,.1)}
.form-lead{position:absolute;left:14px;top:16px;font-size:8.7px;font-weight:600;white-space:nowrap}
.form-lead span{font-weight:300;color:var(--muted);font-size:7px;margin-left:3px}
.field{position:absolute;height:18px;border:1px solid var(--line);font-size:6px;font-style:italic;color:var(--muted);padding:5px 7px;font-weight:300}
.btn{position:absolute;left:14px;top:202px;width:82px;height:26px;background:var(--yellow);color:var(--white);font-size:7px;font-weight:700;display:flex;align-items:center;justify-content:center}

/* Footer */
.footer{position:absolute;left:0;top:919px;width:724px;height:281px;background:var(--footer);color:var(--white)}
.col-head{position:absolute;top:33px;font-size:9.2px;font-weight:500}
.col-rule{position:absolute;top:57px;width:122px;height:1px;background:var(--footer-line)}
.col-rule::before{content:"";position:absolute;left:0;top:-.5px;width:28px;height:1.5px;background:var(--yellow)}
.about{position:absolute;left:97px;top:70px;width:124px;font-size:6.3px;line-height:13.6px}
.social{position:absolute;left:97px;top:152px;display:flex;gap:9px}
.services{position:absolute;left:233px;top:70px;list-style:none;font-size:6.3px;line-height:14px}
.services li:first-child{color:var(--yellow)}
.thumb{position:absolute;width:24px;height:24px}
.sub-text{position:absolute;left:504px;top:70px;width:124px;font-size:6.3px;line-height:11px;color:var(--yellow)}
.sub-input{position:absolute;left:504px;top:110px;width:99px;height:23px;background:#2e2e2e;font-size:5.6px;font-style:italic;color:#9a9a9a;padding:8px 5px}
.sub-btn{position:absolute;left:603px;top:110px;width:23px;height:23px;background:var(--yellow);display:flex;align-items:center;justify-content:center}
.sub-note{position:absolute;left:504px;top:142px;width:124px;font-size:6.3px;line-height:11px}
.footer-rule{position:absolute;left:96px;top:187px;width:530px;height:1px;background:var(--footer-line)}
.brand{position:absolute;left:97px;top:212px;display:flex;align-items:center;gap:5px}
.brand .dot{width:32px;height:32px;border-radius:50%;border:2px solid var(--yellow)}
.brand span{font-size:9.5px;font-weight:600;color:var(--yellow);letter-spacing:.3px}
.contact{position:absolute;top:220px}
.contact svg{position:absolute;left:0;top:2px}
.contact h5{position:absolute;left:13px;top:0;font-size:7px;font-weight:600;white-space:nowrap}
.contact p{position:absolute;left:13px;top:12px;font-size:6px;color:#bdbdbd;white-space:nowrap}
</style>
</head>
<body>
<div class="page">

  <h2 class="section-title">LATEST FRESH NEWS<span>.</span></h2>
  <div class="title-rule" style="top:69px"></div>
  <div class="title-rule" style="top:72px;left:356px;width:24px"></div>

  <div class="news-photo" style="left:97px;background:linear-gradient(160deg,#8b8f95,#c9a52a 55%,#3d3d3d)" role="img" aria-label="Warehouse worker driving a yellow forklift"></div>
  <div class="news-photo" style="left:279px;background:linear-gradient(160deg,#3a3a34,#4a4f3c 50%,#22251f)" role="img" aria-label="Close-up of industrial machinery with a link overlay"></div>
  <div class="news-photo" style="left:460px;background:linear-gradient(160deg,#d9dadd,#4f6ea5 45%,#c8323a 80%)" role="img" aria-label="Two engineers in hard hats reviewing plans"></div>

  <article class="news-card" style="left:102px">
    <h3>Valar &amp; Dohaeris<br>Istikam Polefat Iste</h3>
    <div class="rule"></div>
    <p class="meta">February 17, 2019 - by <b>Lena Marsh</b></p>
    <div class="more"><svg width="5" height="6" viewBox="0 0 5 6"><path d="M1 .5 3.5 3 1 5.5" fill="none" stroke="#1f1f1f" stroke-width="1"/></svg></div>
  </article>
  <article class="news-card active" style="left:283px">
    <h3>Valar &amp; Dohaeris<br>Istikam Polefat Iste</h3>
    <div class="rule"></div>
    <p class="meta">February 17, 2019 - by <b>Lena Marsh</b></p>
    <div class="more"><svg width="5" height="6" viewBox="0 0 5 6"><path d="M1 .5 3.5 3 1 5.5" fill="none" stroke="#fff" stroke-width="1"/></svg></div>
  </article>
  <article class="news-card" style="left:464px">
    <h3>Valar &amp; Dohaeris<br>Istikam Polefat Iste</h3>
    <div class="rule"></div>
    <p class="meta">February 17, 2019 - by <b>Lena Marsh</b></p>
    <div class="more"><svg width="5" height="6" viewBox="0 0 5 6"><path d="M1 .5 3.5 3 1 5.5" fill="none" stroke="#1f1f1f" stroke-width="1"/></svg></div>
  </article>

  <section class="partners" aria-label="Partners">
    <div class="badge" style="left:98px" aria-hidden="true"><svg width="62" height="52"><rect x="11" y="6" width="40" height="40" fill="none" stroke="#fff" stroke-width="2"/></svg></div>
    <div class="badge" style="left:190px" aria-hidden="true"><svg width="62" height="52"><circle cx="31" cy="26" r="21" fill="none" stroke="#fff" stroke-width="2"/></svg></div>
    <div class="badge" style="left:283px" aria-hidden="true"><svg width="62" height="52"><rect x="11" y="6" width="40" height="40" fill="none" stroke="#fff" stroke-width="2"/></svg></div>
    <div class="badge" style="left:376px" aria-hidden="true"><svg width="62" height="52"><circle cx="31" cy="26" r="21" fill="none" stroke="#fff" stroke-width="2"/></svg></div>
    <div class="badge" style="left:468px" aria-hidden="true"><svg width="62" height="52"><rect x="11" y="6" width="40" height="40" fill="none" stroke="#fff" stroke-width="2"/></svg></div>
    <div class="badge" style="left:561px" aria-hidden="true"><svg width="62" height="52"><circle cx="31" cy="26" r="21" fill="none" stroke="#fff" stroke-width="2"/></svg></div>
  </section>

  <div class="worker-photo" style="background:linear-gradient(180deg,#ffffff 0%,#e9c23a 8%,#d8b495 16%,#7e9fd6 35%,#6f8fc8 62%,#b99a75 85%,#a58968 100%);border-radius:60px 60px 0 0" role="img" aria-label="Engineer in a yellow hard hat holding a clipboard"></div>

  <h2 class="quote-title">REQUEST QUOTE</h2>
  <div class="quote-rule"></div>

  <div class="feature" style="top:686px">
    <svg width="19" height="19" viewBox="0 0 20 20"><circle cx="10" cy="10" r="7" fill="none" stroke="#1f1f1f" stroke-width="1.2"/><circle cx="10" cy="10" r="3" fill="none" stroke="#1f1f1f" stroke-width="1.2"/><path d="M4 16 9 11" stroke="#1f1f1f" stroke-width="1.4"/></svg>
    <h4>We Are Efficient</h4><div class="sub">Workers</div>
    <p>Swag kogi knausgaard typewriter, port-land freegan intelligentsia man braid</p>
  </div>
  <div class="feature" style="top:760px">
    <svg width="19" height="19" viewBox="0 0 20 20"><path d="M5 8a5 5 0 0 1 10 0z" fill="none" stroke="#1f1f1f" stroke-width="1.2"/><rect x="7" y="8" width="6" height="4" fill="none" stroke="#1f1f1f" stroke-width="1.2"/><path d="M3 19v-3a4 4 0 0 1 4-4h6a4 4 0 0 1 4 4v3" fill="none" stroke="#1f1f1f" stroke-width="1.2"/></svg>
    <h4>We Are Trusted</h4><div class="sub">Engineers</div>
    <p>Swag kogi knausgaard typewriter, port-land freegan intelligentsia man braid</p>
  </div>
  <div class="feature" style="top:834px">
    <svg width="19" height="19" viewBox="0 0 20 20"><circle cx="10" cy="10" r="7" fill="none" stroke="#1f1f1f" stroke-width="1.2"/><circle cx="10" cy="10" r="3" fill="none" stroke="#1f1f1f" stroke-width="1.2"/><path d="M4 16 9 11" stroke="#1f1f1f" stroke-width="1.4"/></svg>
    <h4>We Are Efficient</h4><div class="sub">Workers</div>
    <p>Swag kogi knausgaard typewriter, port-land freegan intelligentsia man braid</p>
  </div>

  <form class="quote-form">
    <p class="form-lead">For Business:<span>fill the form and call us</span></p>
    <div class="field" style="left:14px;top:39px;width:88px">First Name</div>
    <div class="field" style="left:111px;top:39px;width:88px">Last Name</div>
    <div class="field" style="left:14px;top:66px;width:88px">E-Mail Address</div>
    <div class="field" style="left:111px;top:66px;width:88px">Phone Number</div>
    <div class="field" style="left:14px;top:93px;width:185px">Type Of Service
      <svg class="abs" style="right:7px;top:6px" width="6" height="5"><path d="M0 0h6L3 5z" fill="#777"/></svg></div>
    <div class="field" style="left:14px;top:120px;width:185px;height:63px">Type Your Message Here...</div>
    <div class="btn">REQUEST QUOTE</div>
  </form>

  <footer class="footer">
    <h4 class="col-head" style="left:97px">About Us</h4>
    <h4 class="col-head" style="left:233px">Our Services</h4>
    <h4 class="col-head" style="left:370px">Recent Posts</h4>
    <h4 class="col-head" style="left:504px">Subscribe Us</h4>
    <div class="col-rule" style="left:97px"></div>
    <div class="col-rule" style="left:233px"></div>
    <div class="col-rule" style="left:369px"></div>
    <div class="col-rule" style="left:504px"></div>

    <p class="about">Over 24 years with every experience and knowledge of international standards, and technological changes and industrial systems, we are dedicated to provide the best and economical solutions to our valued customers</p>
    <div class="social" aria-label="Social links">
      <svg width="4" height="4"><rect width="4" height="4" fill="#fff"/></svg>
      <svg width="4" height="4"><rect width="4" height="4" fill="#fff"/></svg>
      <svg width="4" height="4"><rect width="4" height="4" fill="#fff"/></svg>
    </div>

    <ul class="services">
      <li>Valar Dolor Posteam Iftiras</li><li>Valar Dolor Posteam Iftiras</li><li>Valar Dolor Posteam Iftiras</li><li>Valar Dolor Posteam Iftiras</li><li>Valar Dolor Posteam Iftiras</li><li>Valar Dolor Posteam Iftiras</li><li>Valar Dolor Posteam Iftiras</li>
    </ul>

    <div class="thumb" style="left:370px;top:70px;background:linear-gradient(135deg,#c83a2e,#e8e8e8 60%,#8a8a8a)" role="img" aria-label="Post photo: rolled plans"></div>
    <div class="thumb" style="left:402px;top:70px;background:linear-gradient(135deg,#c83a2e,#e8e8e8 60%,#8a8a8a)" role="img" aria-label="Post photo: rolled plans"></div>
    <div class="thumb" style="left:434px;top:70px;background:linear-gradient(135deg,#c83a2e,#e8e8e8 60%,#8a8a8a)" role="img" aria-label="Post photo: rolled plans"></div>
    <div class="thumb" style="left:465px;top:70px;background:linear-gradient(135deg,#c83a2e,#e8e8e8 60%,#8a8a8a)" role="img" aria-label="Post photo: rolled plans"></div>
    <div class="thumb" style="left:370px;top:102px;background:linear-gradient(160deg,#e9c23a,#e4e2dc 55%,#a79b82)" role="img" aria-label="Post photo: workers on site"></div>
    <div class="thumb" style="left:402px;top:102px;background:linear-gradient(160deg,#e9c23a,#e4e2dc 55%,#a79b82)" role="img" aria-label="Post photo: workers on site"></div>
    <div class="thumb" style="left:434px;top:102px;background:linear-gradient(160deg,#e9c23a,#e4e2dc 55%,#a79b82)" role="img" aria-label="Post photo: workers on site"></div>
    <div class="thumb" style="left:465px;top:102px;background:linear-gradient(160deg,#e9c23a,#e4e2dc 55%,#a79b82)" role="img" aria-label="Post photo: workers on site"></div>
    <div class="thumb" style="left:370px;top:134px;background:linear-gradient(160deg,#6d5a44,#f08a2a 55%,#d5d5d5)" role="img" aria-label="Post photo: crew in safety vests"></div>
    <div class="thumb" style="left:402px;top:134px;background:linear-gradient(160deg,#6d5a44,#f08a2a 55%,#d5d5d5)" role="img" aria-label="Post photo: crew in safety vests"></div>
    <div class="thumb" style="left:434px;top:134px;background:linear-gradient(160deg,#6d5a44,#f08a2a 55%,#d5d5d5)" role="img" aria-label="Post photo: crew in safety vests"></div>
    <div class="thumb" style="left:465px;top:134px;background:linear-gradient(160deg,#6d5a44,#f08a2a 55%,#d5d5d5)" role="img" aria-label="Post photo: crew in safety vests"></div>

    <p class="sub-text">Sign up today for hints, tips and the latest product news - plus exclusive, of special offers</p>
    <div class="sub-input">Enter Your E-mail Here</div>
    <div class="sub-btn"><svg width="8" height="6" viewBox="0 0 8 6"><rect width="8" height="6" fill="#fff"/><path d="M0 0 4 3.5 8 0" fill="none" stroke="#f3b11e" stroke-width=".8"/></svg></div>
    <p class="sub-note">Lorem ipsum dolor valar dohaeris ifsitari doker imast after one</p>

    <div class="footer-rule"></div>

    <div class="brand"><div class="dot"></div><span>Harbor Seal Works</span></div>

    <div class="contact" style="left:234px">
      <svg width="12" height="13" viewBox="0 0 24 24"><path d="M6.6 10.8a15 15 0 0 0 6.6 6.6l2.2-2.2a1 1 0 0 1 1-.25 11.4 11.4 0 0 0 3.6.57 1 1 0 0 1 1 1V20a1 1 0 0 1-1 1A17 17 0 0 1 3 4a1 1 0 0 1 1-1h3.5a1 1 0 0 1 1 1c0 1.25.2 2.45.57 3.57a1 1 0 0 1-.25 1z" fill="#f3b11e"/></svg>
      <h5>Have A Question? Call Us</h5><p>+ 0 555 010 274</p>
    </div>
    <div class="contact" style="left:371px">
      <svg width="11" height="15" viewBox="0 0 12 16"><path d="M6 0a6 6 0 0 1 6 6c0 4.5-6 10-6 10S0 10.5 0 6a6 6 0 0 1 6-6z" fill="#f3b11e"/><circle cx="6" cy="6" r="2.2" fill="#232323"/></svg>
      <h5 style="left:19px">Our Office Is Located At</h5><p style="left:19px">Tidewater Road 42, Unit 9</p>
    </div>
    <div class="contact" style="left:505px">
      <svg width="14" height="11" viewBox="0 0 14 10"><rect width="14" height="10" rx="1" fill="#f3b11e"/><path d="M0 1 7 6 14 1" fill="none" stroke="#232323" stroke-width="1"/></svg>
      <h5 style="left:21px">Got Any Request? Write us</h5><p style="left:21px">hello@harborsealworks.example</p>
    </div>
  </footer>
</div>
</body>
</html>
```